Allied Health team of Physiotherapists & Occupational Therapists seek a business card design

We have our new logo, we now need our new business cards and stationary. Tidewell: Oedema & Family Clinic is seeking a generic card design to represent our whole team and individual cards for each therapist that incorporates our new logo to communicate our holistic approach that is calming, nuturing, supportive and welcoming.
Our Physiotherapists and Occupational Therapists assess, treat and provide education for people who are at risk of or who have lymphoedema. This is often as a result of treatment for cancer. We provide pre-operative and post-operative management and cancer rehabilitation in our Pilates studio. Our team also consists of Physiotherapists who have a strong interest in pelvic floor and continence management for both men and women.

Target Market(s)

Mainly women health conscious

Industry/Entity Type

Allied Health: Physiotherapy / Occupational Therapy

Contact Information for Business Card

Address: 14 Gallivant Ave Marlowe Bay 3207 Phone: 84316570 fax: 8431 6578 Email: info@tidewellcareservices.com.au Website: tidewellcareservices.com.au Facebook address: facebook.com/TidewellOedemaAndFamilyCareClinic. Room to write appointments. Individual cards need to have name, office email and individual email and professional details

Requirements
Must have
• Logo as per uploaded documents

```html
<!DOCTYPE html>
<html lang="en">
<head>
<meta charset="utf-8">
<title>Tidewell Business Card</title>
<link rel="stylesheet" href="https://fonts.googleapis.com/css2?family=Cinzel:wght@700&family=Lato:ital,wght@0,400;0,700;0,900;1,400;1,700&display=swap">
<style>
:root{
  --page:#2a2a2a;
  --peach-light:#fbbf95;
  --peach:#f8ad7b;
  --peach-text:#f5a574;
  --sage:#c3cdc0;
  --white:#ffffff;
  --ink:#555555;
  --faint:#fdf1e8;
}
*{margin:0;padding:0;box-sizing:border-box}
html,body{width:1200px;height:1200px;overflow:hidden;background:var(--page)}
.canvas{position:relative;width:1200px;height:1200px}
.card{position:absolute;left:200px;width:800px;height:457px;border-radius:26px;overflow:hidden;background:var(--white);font-family:"Lato",sans-serif}
.card--front{top:87px}
.card--back{top:656px}
.card__shape{position:absolute;inset:0}
.profile{position:absolute;left:47px;top:174px;color:var(--white)}
.profile__name{font-family:"Cinzel",serif;font-weight:700;font-size:26px;letter-spacing:.5px}
.profile__role{font-size:17px;margin-top:2px}
.contact{list-style:none;margin-top:20px;font-size:18.5px;line-height:25px}
.contact li{display:flex;align-items:flex-start;gap:9px}
.contact li+li.gap{margin-top:12px}
.contact svg{width:16px;height:16px;margin-top:4px;flex:none;fill:var(--white)}
.brand{position:absolute;left:508px;top:145px;display:flex;align-items:center;gap:12px;color:var(--peach-text);font-size:46px;font-weight:400}
.brand__dot{width:18px;height:18px;border-radius:50%;background:var(--sage)}
.watermark{position:absolute;left:0;right:0;top:175px;text-align:center;font-size:100px;color:var(--faint);font-weight:400}
.appt__title{position:absolute;left:53px;top:38px;font-size:30px;color:var(--peach-text);font-weight:400}
.book{position:absolute;left:582px;top:41px;width:155px;height:31px;border-radius:8px;background:var(--peach);color:var(--white);font-weight:900;font-style:italic;font-size:19px;text-align:center;line-height:31px}
.field{position:absolute;display:flex;align-items:baseline;color:var(--peach-text);font-size:18px}
.field__line{border-bottom:2px dotted #9a9a9a;height:1px;margin:0 6px}
.notice{position:absolute;left:90px;right:90px;top:322px;text-align:center;font-style:italic;font-size:17px;line-height:23px;color:var(--ink)}
.footer-url{position:absolute;left:0;right:0;top:422px;text-align:center;color:var(--white);font-style:italic;font-weight:700;font-size:19px;letter-spacing:4.5px}
</style>
</head>
<body>
<div class="canvas">

  <section class="card card--front">
    <svg class="card__shape" viewBox="0 0 800 457" aria-hidden="true">
      <defs>
        <linearGradient id="peachFade" x1="0" y1="0" x2="0" y2="1">
          <stop offset="0" stop-color="#fbbf95"/>
          <stop offset="1" stop-color="#f8ab78"/>
        </linearGradient>
      </defs>
      <path d="M398 6 C346 34 330 84 354 122 C392 182 468 262 460 342 C455 400 432 440 410 457" fill="none" stroke="#c3cdc0" stroke-width="7"/>
      <path d="M0 0 H400 C342 26 322 80 346 120 C382 180 456 260 448 340 C444 400 420 440 402 457 H0 Z" fill="url(#peachFade)" stroke="#ffffff" stroke-width="3"/>
    </svg>
    <div class="profile">
      <h1 class="profile__name">MAREN HOLT</h1>
      <p class="profile__role">Physiotherapist</p>
      <ul class="contact">
        <li><svg viewBox="0 0 16 16"><path d="M8 0a5.5 5.5 0 0 0-5.5 5.5C2.5 9.6 8 16 8 16s5.5-6.4 5.5-10.5A5.5 5.5 0 0 0 8 0zm0 8a2.5 2.5 0 1 1 0-5 2.5 2.5 0 0 1 0 5z"/></svg><span>14 Gallivant Ave<br>Marlowe Bay 3207</span></li>
        <li class="gap"><svg viewBox="0 0 16 16"><path d="M3.6 1l2.6 3-1.4 2c.9 2 2.4 3.5 4.4 4.4l2-1.4 3 2.6-1.6 2.6C7 14 2 9 1 2.6z"/></svg><span>8431 6570</span></li>
        <li><svg viewBox="0 0 16 16"><path d="M4 1h7v4H4zM1 6h14v6h-3v3H4v-3H1zm4 5v3h6v-3z"/></svg><span>8431 6578</span></li>
        <li><svg viewBox="0 0 16 16"><path d="M1 3h14v1L8 9 1 4zm0 3l7 5 7-5v7H1z"/></svg><span>info@tidewellcareservices.com.au</span></li>
        <li><svg viewBox="0 0 16 16"><path d="M8 1a7 7 0 1 0 0 14A7 7 0 0 0 8 1zm-1 12.4A5.5 5.5 0 0 1 3 6l2 2v1l2 2zm4.5-1.6c-.3-.6-1-1-1.5-1h-1V9H6V7h2V5h1.5V3.6a5.5 5.5 0 0 1 2 8.2z"/></svg><span>tidewellcareservices.com.au</span></li>
      </ul>
    </div>
    <div class="brand"><span class="brand__dot"></span><span>Tidewell</span></div>
  </section>

  <section class="card card--back">
    <div class="watermark" aria-hidden="true">Tidewell</div>
    <h2 class="appt__title">Next Appointment</h2>
    <div class="book">Book Online</div>

    <div class="field" style="left:53px;top:102px"><span>Name :</span><span class="field__line" style="width:590px;margin-left:20px"></span></div>
    <div class="field" style="left:53px;top:158px"><span>Date :</span><span class="field__line" style="width:308px;margin-left:14px;margin-right:2px"></span><span>Time :</span><span class="field__line" style="width:165px"></span><span>AM/PM</span></div>
    <div class="field" style="left:53px;top:212px"><span>Note :</span><span class="field__line" style="width:600px;margin-left:14px"></span></div>
    <div class="field" style="left:53px;top:262px"><span class="field__line" style="width:678px;margin:0"></span></div>

    <p class="notice">Please give me 24 hours notice if you are unable to keep your appointment or a cancellation fee may be charged.</p>

    <svg class="card__shape" viewBox="0 0 800 457" aria-hidden="true">
      <path d="M0 405 C120 378 240 392 380 402 C560 414 680 398 760 370" fill="none" stroke="#c3cdc0" stroke-width="5"/>
      <path d="M0 412 C120 388 240 398 380 408 C560 420 700 400 800 345 V457 H0 Z" fill="#f8ad7b"/>
    </svg>
    <p class="footer-url">TIDEWELLCARESERVICES.COM.AU</p>
  </section>

</div>
</body>
</html>
```